Business Card Design for a Personal Trainer

I need a business card design for my job as a personal trainer. It should have a unique, modern and exclusive design. On the front there should be only my logo with my name and my job. 0162/3819204 Tobias Lendhart Wiesengrundweg 14 80417 Munich Germany The most important contact information is the web adress. it can be bigger than the rest, but its not necessary. The card should be 8,5cmx5,5cm big. Font: Roboto. Colors: black, white, gray, 56c1ff.

```html
<!DOCTYPE html>
<html lang="de">
<head>
<meta charset="utf-8">
<title>Tobias Lendhart – Visitenkarte</title>
<link href="https://fonts.googleapis.com/css2?family=Roboto:wght@300;400;500;700&display=swap" rel="stylesheet">
<style>
  :root {
    --page: #f4f4f4;
    --card: #2a2a2a;
    --white: #ffffff;
    --text-soft: #e6e6e6;
    --faint: #3f3c3c;
    --photo-light: #6a6a6a;
    --photo-dark: #2c2c2c;
  }
  * { margin: 0; padding: 0; box-sizing: border-box; }
  html, body {
    width: 1195px; height: 1200px; overflow: hidden;
    background: var(--page);
    font-family: "Roboto", sans-serif;
  }
  .sheet {
    position: relative; width: 1195px; height: 1200px;
    display: flex; justify-content: center; align-items: center; gap: 40px;
  }
  .card {
    position: relative; width: 540px; height: 350px;
    background: var(--card); overflow: hidden;
    box-shadow: 0 3px 10px rgba(0,0,0,.35);
    color: var(--white);
  }
  .card-corners { position: absolute; inset: 0; width: 100%; height: 100%; z-index: 2; }
  .card-corners polygon { fill: var(--white); }

  /* back side */
  .faint-name {
    position: absolute; left: 52px; top: 50px;
    font-weight: 500; font-size: 22px; letter-spacing: 1px;
    color: var(--faint); white-space: nowrap;
    display: flex; align-items: center; gap: 9px;
  }
  .faint-name .mark { width: 13px; height: 13px; background: var(--faint); flex: none; }
  .contact-list {
    position: absolute; left: 44px; top: 146px;
    list-style: none; font-weight: 300; font-size: 17px; letter-spacing: .6px;
    color: var(--text-soft);
  }
  .contact-list li { display: flex; align-items: flex-start; gap: 10px; margin-bottom: 10px; line-height: 22px; }
  .contact-list svg { width: 13px; height: 13px; margin-top: 5px; flex: none; fill: var(--text-soft); }
  .web {
    position: absolute; left: 30px; top: 280px;
    font-weight: 700; font-size: 18px; letter-spacing: 1.6px;
  }
  .portrait {
    position: absolute; left: 320px; top: 28px; width: 220px; height: 322px;
    background: radial-gradient(ellipse at 50% 45%, var(--photo-light) 0%, var(--photo-dark) 75%);
    border-radius: 60px 60px 0 0;
    z-index: 1;
  }

  /* front side */
  .brand {
    position: absolute; left: 0; right: 0; top: 160px;
    font-weight: 400; font-size: 34px; letter-spacing: .5px; line-height: 40px;
    display: flex; justify-content: center; align-items: center; gap: 12px;
  }
  .brand .mark { width: 18px; height: 18px; background: var(--white); }
  .owner {
    position: absolute; left: 0; right: 0; top: 234px; text-align: center;
  }
  .owner-name { font-weight: 700; font-size: 23px; letter-spacing: 1.4px; line-height: 28px; }
  .owner-role { font-weight: 300; font-size: 18px; letter-spacing: 1px; color: var(--text-soft); line-height: 24px; }
</style>
</head>
<body>
<main class="sheet">

  <section class="card card-back" aria-label="Rückseite">
    <div class="faint-name" aria-hidden="true"><span class="mark"></span>TOBIAS LENDHART</div>

    <ul class="contact-list">
      <li>
        <svg viewBox="0 0 24 24"><path d="M6.6 10.8a15.2 15.2 0 0 0 6.6 6.6l2.2-2.2c.3-.3.7-.4 1-.2 1.1.4 2.3.6 3.6.6.6 0 1 .4 1 1V20c0 .6-.4 1-1 1A17 17 0 0 1 3 4c0-.6.4-1 1-1h3.5c.6 0 1 .4 1 1 0 1.3.2 2.5.6 3.6.1.3 0 .7-.2 1z"/></svg>
        <span>0162/3819204</span>
      </li>
      <li>
        <svg viewBox="0 0 24 24"><path d="M2 5h20v14H2z M4 7l8 6 8-6" fill="none" stroke="#e6e6e6" stroke-width="2.4"/></svg>
        <span>t.lendhart@mailpost.de</span>
      </li>
      <li>
        <svg viewBox="0 0 24 24"><path d="M12 2a7 7 0 0 0-7 7c0 5.2 7 13 7 13s7-7.8 7-13a7 7 0 0 0-7-7zm0 9.5A2.5 2.5 0 1 1 12 6.5a2.5 2.5 0 0 1 0 5z"/></svg>
        <span>Wiesengrundweg 14<br>880417 München</span>
      </li>
    </ul>

    <p class="web">www.lendhart-training.de</p>

    <div class="portrait" role="img" aria-label="Schwarz-Weiß-Porträt des Trainers mit verschränkten Armen"></div>

    <svg class="card-corners" viewBox="0 0 540 350" aria-hidden="true">
      <polygon points="0,0 89,0 0,97"/>
      <polygon points="375,350 540,350 540,279"/>
    </svg>
  </section>

  <section class="card card-front" aria-label="Vorderseite">
    <div class="brand"><span class="mark"></span>TOBIAS LENDHART</div>
    <div class="owner">
      <p class="owner-name">Tobias Lendhart</p>
      <p class="owner-role">Personal Trainer</p>
    </div>
    <svg class="card-corners" viewBox="0 0 540 350" aria-hidden="true">
      <polygon points="0,0 93,0 0,80"/>
      <polygon points="426,350 540,350 540,279"/>
    </svg>
  </section>

</main>
</body>
</html>
```